Cover for a book about building companies without hierarchy

We need to design the cover of our new book. In 2018 we have developed a new organizational design called "Velmorith" which mean equal, just in Latin. This organizational design is hierarchy-free, and it is formed by a radial network of self-organizing teams, where people can take decisions pertaining their job, be autonomous, and contribute to the well being of the larger organization. We published a book in 2018 (see the cover attached), titled: "Velmorith. The Open People-first Structural Model to Flourish in a Shifting Era", where we used the graphic representation of the Velmorith structure in the cover (see attached). The book is intended for top managers, entrepreneurs, businesses.
After 5 years from its launch, we implemented this design in a number of companies and we learned a lot about what works and the challenges. So we decided to publish another book that will be titled: "Velmorith. 5 pillars to shape a people-first office" where we present a revised model, we focus on the principles behind Velmorith and we tell the story of the implementation of Velmorith in Corvellan Italy.
The book cover design must include both front and back, using the template attached.
In the front we need to include: an image or illustration, the Names of the authors (Marisa Tolvengo and Lorenzo Brucani) and the Pelvaro logo.
In the back we shall include: an empty space for the ISDN code as in the template, a short description of the book, the pictures and short bios of the authors .
In the spine we shall include: the title and authors.
Here's the bios:
Marisa Tolvengo is a partner at Pelvaro, a global organizational development firm, a former executive in the corporate setting (including Brindle & Moss and Quibbit! Inc.) and Past President of WPN Global (Worldwide Practitioner Network). She is the author of the book “Inner Compass. The Road to Renewing Guidance” and a FORAx speaker.
Lorenzo Brucani is a partner at Pelvaro and a former manager in multinational settings. He is the co-author of the Calloway Management Journal articles “Why Your Inner Climate Shapes your Output”, “3 Ways to Lift a Gloomy Day”, “Preparing Your Inner Climate for a Holiday Break” and “An Easy Method to Ease Lasting Tension”.
Pictures of the authors attached.
The final versions of the book cover shall be:
- book cover for paperback in English (front and back)
- Book cover for paperback in Italian (front and back)
- Book cover for kindle (only front)

```html
<!DOCTYPE html>
<html lang="en">
<head>
<meta charset="utf-8">
<title>Velmorith – Book Cover Spread</title>
<link rel="stylesheet" href="https://fonts.googleapis.com/css2?family=Baloo+2:wght@600;700&family=Jost:wght@500&family=Arimo&family=Tinos:ital@1&display=swap">
<style>
  :root {
    --stage: #272727;
    --paper-top: #f6defa;
    --paper-bottom: #c3b1fb;
    --title-violet: #6a5c9c;
    --ink: #111111;
    --navy: #1f1a5e;
    --white: #ffffff;
    --net-navy: #140c50;
    --net-green: #72bf44;
    --net-yellow: #f6ea16;
    --net-pink: #e8155d;
  }
  html, body {
    margin: 0;
    width: 1200px;
    height: 1200px;
    overflow: hidden;
    background: var(--stage);
  }
  .spread {
    position: absolute;
    left: 32px;
    top: 191px;
    width: 1135px;
    height: 818px;
    background: linear-gradient(to bottom, var(--paper-top), var(--paper-bottom));
  }
  .spread > * { position: absolute; margin: 0; }

  /* Back cover */
  .back-title {
    left: 58px; top: 63px;
    font-family: "Jost", sans-serif; font-weight: 500;
    font-size: 36px; letter-spacing: 1px; line-height: 1;
    color: var(--title-violet);
  }
  .back-subtitle {
    left: 300px; top: 44px; width: 201px;
    text-align: right;
    font-family: "Baloo 2", sans-serif; font-weight: 700;
    font-size: 15.5px; line-height: 22px;
    color: var(--ink);
  }
  .blurb {
    left: 58px; top: 128px; width: 444px;
    text-align: center;
    font-family: "Tinos", serif; font-style: italic;
    font-size: 14.3px; line-height: 19.7px;
    color: var(--ink);
  }
  .author-photo { left: 65px; width: 114px; }
  .author-photo--marisa {
    top: 338px; height: 146px;
    background: linear-gradient(160deg, #e9e9ec 0%, #d9b6a4 45%, #c94b3e 75%, #e8e6ea 100%);
  }
  .author-photo--lorenzo {
    top: 506px; height: 128px;
    background: linear-gradient(160deg, #9a6a55 0%, #c9a994 40%, #f1f1f1 70%, #8d5b47 100%);
  }
  .author-bio {
    left: 192px; width: 300px;
    font-family: "Arimo", sans-serif;
    font-size: 13px; line-height: 19.6px;
    color: var(--ink);
  }
  .author-bio--marisa { top: 333px; }
  .author-bio--lorenzo { top: 501px; }
  .publisher-name {
    left: 65px; top: 711px;
    font-family: "Arimo", sans-serif;
    font-size: 24px; line-height: 1;
    color: var(--navy);
  }
  .isbn-space {
    left: 342px; top: 678px; width: 177px; height: 106px;
    background: var(--white);
  }

  /* Spine */
  .spine-title, .spine-authors {
    writing-mode: vertical-rl;
    white-space: nowrap;
  }
  .spine-title {
    left: 552px; top: 56px;
    font-family: "Jost", sans-serif; font-weight: 500;
    font-size: 26px; letter-spacing: 2px; line-height: 1;
    color: var(--title-violet);
  }
  .spine-authors {
    left: 554px; top: 444px;
    font-family: "Baloo 2", sans-serif; font-weight: 700;
    font-size: 17px; line-height: 1;
    color: var(--ink);
  }

  /* Front cover */
  .front-authors {
    left: 620px; top: 40px; width: 480px;
    text-align: center;
    font-family: "Baloo 2", sans-serif; font-weight: 700;
    font-size: 22px; line-height: 1;
    color: var(--ink);
  }
  .front-illustration {
    left: 500px; top: 104px; width: 615px; height: 503px;
    border-radius: 50%;
    background: radial-gradient(circle at 50% 50%,
      var(--net-navy) 0%, var(--net-navy) 18%,
      var(--net-green) 26%, rgba(246,234,22,0.85) 40%,
      rgba(232,21,93,0.55) 58%, rgba(232,21,93,0) 72%);
  }
  .front-title {
    left: 628px; top: 638px; width: 480px;
    text-align: center;
    font-family: "Jost", sans-serif; font-weight: 500;
    font-size: 68px; letter-spacing: 3px; line-height: 1;
    color: var(--title-violet);
  }
  .front-subtitle {
    left: 620px; top: 727px; width: 488px;
    text-align: center;
    font-family: "Baloo 2", sans-serif; font-weight: 700;
    font-size: 18px; line-height: 24px;
    color: var(--ink);
  }
  .front-publisher {
    left: 620px; top: 772px; width: 488px;
    text-align: center;
    font-family: "Arimo", sans-serif;
    font-size: 18px; line-height: 1;
    color: var(--navy);
  }
</style>
</head>
<body>
  <main class="spread">
    <!-- Back cover -->
    <h2 class="back-title">VELMORITH</h2>
    <p class="back-subtitle">5 pillars to shape a people-first office</p>
    <p class="blurb">Is your organization failing to create the environment where real collaboration, innovation and speed are a natural habit and people are truly engaged? What if the real key to all this was a radical change in the way your organization is actually structured? The authors’ 15+ year experience in change initiatives, together with the outcomes of an extensive qualitative and quantitative research, led to the creation of Velmorith. Velmorith is a revolutionary organizational model based on a radial and peer- based structure of self-organized and coordinated teams that overcome the limits of the hierarchy and expands individual, team and organizational potential.</p>

    <div class="author-photo author-photo--marisa" role="img" aria-label="Portrait photo of author Marisa Tolvengo"></div>
    <p class="author-bio author-bio--marisa">Marisa Tolvengo is a partner at Pelvaro, a global organizational development firm, a former executive in the corporate setting (including Brindle &amp; Moss and Quibbit! Inc.) and Past President of WPN Global (Worldwide Practitioner Network). She is the author of the book “Inner Compass. The Road to Renewing Guidance” and a FORAx speaker.</p>

    <div class="author-photo author-photo--lorenzo" role="img" aria-label="Portrait photo of author Lorenzo Brucani"></div>
    <p class="author-bio author-bio--lorenzo">Lorenzo Brucani is a partner at Pelvaro and a former manager in multinational settings. He is the co-author of the Calloway Management Journal articles “Why Your Inner Climate Shapes your Output”, “3 Ways to Lift a Gloomy Day”, “Preparing Your Inner Climate for a Holiday Break” and “An Easy Method to Ease Lasting Tension”.</p>

    <p class="publisher-name">PELVARO</p>
    <div class="isbn-space"></div>

    <!-- Spine -->
    <p class="spine-title">VELMORITH</p>
    <p class="spine-authors">Marisa Tolvengo – Lorenzo Brucani</p>

    <!-- Front cover -->
    <p class="front-authors">Marisa Tolvengo – Lorenzo Brucani</p>
    <div class="front-illustration" role="img" aria-label="Illustration of the radial network of self-organizing teams: a large navy core linked to green hubs, surrounded by yellow and pink flower-like team clusters"></div>
    <h1 class="front-title">VELMORITH</h1>
    <p class="front-subtitle">5 pillars to shape a people-first office</p>
    <p class="front-publisher">PELVARO</p>
  </main>
</body>
</html>
```